Stationary design for boutique production house

We need a stationary design for our production house, 'Lorno Productions' based in Singapore. We produce microfilms as well as podcasts, talkshows and events. Our logo is a stylized icon of our director, who is also the executive producer and host of our programs, Lorno. Our main company colors are Red, Black and white. We would like a clean, minimalist design incorporating our existing company logo that conveys a sense of urbanism and elegance.

Logo and font files are attached. f

Target Market(s)

We focus on lifestyle media rather than entertainment.

Industry/Entity Type

Boutique

Font styles to use
Serif
Sans Serif

Colors
ec1f27
ffffff
000000

Requirements
Must have
• Our company logo and at least one of our company colors.
Nice to have
• Our address and contact information.
Should not have
• Changes made to the company logo (using only certain parts of it is fine though)

```html
<!DOCTYPE html>
<html lang="en">
<head>
<meta charset="utf-8">
<title>Lorno Productions – Business Card</title>
<link href="https://fonts.googleapis.com/css2?family=Jost:wght@400;500&display=swap" rel="stylesheet">
<style>
  :root {
    --brand-red: #ec1f27;
    --deep-red: #b3121a;
    --ink: #111111;
    --white: #ffffff;
    --frost: #e9eaec;
    --frost-edge: #d3d5d8;
    --page: #f2f2f2;
  }
  html, body {
    margin: 0;
    width: 1200px;
    height: 969px;
    overflow: hidden;
    background: var(--page);
    font-family: "Jost", sans-serif;
  }
  .business-card {
    position: absolute;
    left: 100px;
    top: 200px;
    width: 1000px;
    height: 568px;
    border-radius: 26px;
    overflow: hidden;
    background: linear-gradient(160deg, #f6f6f7 0%, var(--frost) 60%, #dcdee1 100%);
    box-shadow: 0 10px 30px rgba(0,0,0,0.15);
  }
  .card-shapes {
    position: absolute;
    inset: 0;
    width: 100%;
    height: 100%;
  }
  .contact-side {
    position: absolute;
    left: 60px;
    top: 0;
    color: var(--white);
  }
  .person-name {
    position: absolute;
    top: 76px;
    margin: 0;
    font-size: 34px;
    font-weight: 400;
    letter-spacing: 1px;
    white-space: nowrap;
  }
  .person-role {
    position: absolute;
    top: 124px;
    margin: 0;
    font-size: 25px;
    font-weight: 400;
    letter-spacing: 0.5px;
    white-space: nowrap;
  }
  .postal-address {
    position: absolute;
    top: 210px;
    margin: 0;
    font-style: normal;
    font-size: 24px;
    line-height: 34px;
    white-space: nowrap;
  }
  .contact-list {
    position: absolute;
    top: 302px;
    margin: 0;
    padding: 0;
    list-style: none;
    font-size: 23px;
    white-space: nowrap;
  }
  .contact-list li {
    display: flex;
    align-items: center;
    height: 41px;
  }
  .contact-list svg {
    width: 22px;
    height: 22px;
    margin-right: 24px;
    fill: var(--white);
  }
  .contact-list .is-muted { opacity: 0.75; }
  .brand-mark {
    position: absolute;
    left: 560px;
    top: 250px;
    width: 360px;
    display: flex;
    align-items: center;
    justify-content: center;
    gap: 16px;
  }
  .brand-dot {
    width: 22px;
    height: 22px;
    border-radius: 50%;
    background: var(--brand-red);
  }
  .brand-name {
    margin: 0;
    font-size: 40px;
    font-weight: 500;
    color: var(--ink);
    letter-spacing: 1px;
    white-space: nowrap;
  }
</style>
</head>
<body>
  <div class="business-card">
    <svg class="card-shapes" viewBox="0 0 1000 568" preserveAspectRatio="none" aria-hidden="true">
      <defs>
        <linearGradient id="redPanel" x1="0" y1="0" x2="1" y2="1">
          <stop offset="0" stop-color="#d8202a"/>
          <stop offset="0.6" stop-color="#c3151e"/>
          <stop offset="1" stop-color="#e0262e"/>
        </linearGradient>
      </defs>
      <path d="M520 0 C 500 130, 500 270, 545 390 C 570 460, 585 520, 605 568 L 560 568 C 500 440, 455 300, 480 150 C 490 90, 505 40, 520 0 Z" fill="var(--ink)"/>
      <path d="M0 0 L505 0 C 465 110, 450 230, 470 340 C 485 430, 510 500, 540 568 L0 568 Z" fill="url(#redPanel)"/>
    </svg>

    <div class="contact-side">
      <h1 class="person-name">DANIEL TAN</h1>
      <p class="person-role">CEO/FOUNDER</p>
      <address class="postal-address">42 Keppel Row<br>Singapore 089123</address>
      <ul class="contact-list">
        <li><svg viewBox="0 0 24 24"><path d="M6.6 10.8a15 15 0 0 0 6.6 6.6l2.2-2.2c.3-.3.7-.4 1-.2 1.1.4 2.3.6 3.6.6.6 0 1 .4 1 1V20c0 .6-.4 1-1 1A17 17 0 0 1 3 4c0-.6.4-1 1-1h3.5c.6 0 1 .4 1 1 0 1.3.2 2.5.6 3.6.1.3 0 .7-.2 1z"/></svg>612 345 7781</li>
        <li><svg viewBox="0 0 24 24"><path d="M7 1h10a2 2 0 0 1 2 2v18a2 2 0 0 1-2 2H7a2 2 0 0 1-2-2V3a2 2 0 0 1 2-2zm0 3v14h10V4zm5 15.5a1 1 0 1 0 0 2 1 1 0 0 0 0-2z"/></svg>845 210 6637</li>
        <li><svg viewBox="0 0 24 24"><path d="M6 2h12v5H6zM4 8h16a2 2 0 0 1 2 2v7h-4v5H6v-5H2v-7a2 2 0 0 1 2-2zm4 7v5h8v-5z"/></svg>473 905 2186</li>
        <li class="is-muted"><svg viewBox="0 0 24 24"><path d="M2 5h20v14H2zm2 2v.5l8 5 8-5V7l-8 5z"/></svg>hello@lornoprod.com</li>
        <li class="is-muted"><svg viewBox="0 0 24 24"><path d="M12 2a10 10 0 1 0 0 20 10 10 0 0 0 0-20zm-1 17.9A8 8 0 0 1 4.2 10L9 14.8v1a2 2 0 0 0 2 2zm6.9-2.5A2 2 0 0 0 16 16h-1v-3a1 1 0 0 0-1-1H8v-2h2a1 1 0 0 0 1-1V7h2a2 2 0 0 0 2-2v-.4a8 8 0 0 1 2.9 12.8z"/></svg>www.lornoprod.com</li>
      </ul>
    </div>

    <div class="brand-mark">
      <span class="brand-dot"></span>
      <p class="brand-name">Lorno Productions</p>
    </div>
  </div>
</body>
</html>
```